Edgey, Modern Air Conditioning Website

Bramble Works
current website - www.kelvaroom.nz
Facelane - www.facebook.com/bramwrk

We really have no idea about webdesign etc we are Engineers not Graphic artists or creative writers. We really just want a edgy, modern website completed on our behalf

We can get pictures of projects as directed or happy for you to use stock images of Talvoro Mecha NZ (Heatpumps) air conditioning and exposed ducting etc

we would like the website to be heavily based on the below website. I like what they have done with both the site and the app but obviously would need to suit Bramble Works, snowflakes heating cooling etc etc Blue and white to match our logo etc

http://parrowbeams.co.nz/

Need links to contact page:
Bramble Works
27 Harlow Crescent
Petone
Wellington

0800 529 174 (0800BRAMWKS)

Marta.k@bramwks.co.nz

BRAMBLE WORKS
SATISFACTION GAURANTEED

WHY CHOOSE BRAMBLE WORKS
EXPERIENCE COUNTS

We have a team of nationally trained and qualified Refrigeration/HVAC/Electrical Engineers and Technicians based in Petone, Wellington offering services to Wellington, Manuwatu and the Wairarapa. We are factory trained and authorised to design, service and install all major brands including Talvoro, Pelnor, Korrowane Electric, Veltrada and Osmelo units. We extend our installation warranty to match that of the manufacturer’s warranty and specialise in our own diagnostics and repair.

SATISFACTION GUARANTEE
We aim to please and I put my name behind our brand! We will take care of your project from start to finish and offer a unique experience with our 100% satisfaction Guarantee*. We will supply and install your system and if your system is not installed how it was explained or not up to a trades standard we will return to make any the necessary modifications free of charge. We back this service up with our 0% upfront strategy, the power is in your hands. We will only invoice you once the installation has been completed up to a BRAMBLE WORKS standard.

LOW PRESSURE SALES
Nobody likes the vacuum salesmen’s techniques and neither do we. We will come to your home or business to provide a free measure and quote. Our experience will insure this is a quick and painless experience, you will be provided with expert advice from a qualified Refrigeration Engineer, not a car salesmen turned “Heating Guru”. We will follow up with an email providing our best price straight up, installation details and online brochures. We won’t bug you with repeated phone calls and inbox clogging emails. Once we receive confirmation we will issue you with an installation date and typically have your installation completed within 10 working days.

BRANDS
www.talvoromecha.co.nz
www.pelnor.co.nz
http://quellaro.co.nz/

SERVICES
Heatpumps/Air Conditioning – Heat pumps are the most efficient way of using electricity to heat your home, but some are more efficient than others. We will select the right model for your requirements taking into account the capacity required, the visual impact of the system, the style of system, air flow and obviously your personal preferences. We only install the highest quality brands that offer outstanding after sales support. Cassettes, Consoles, Under Ceilings, Ducted, Hiwalls, Multis… Confused? Give us a call.

COMMERCIAL
We have a growing Portfolio of clients that rely on us for their Commercial requirements. We have proven ourselves to be a force to be reckoned with to be able to think outside the square and come up with unique and cost effective solutions to heat and cool large areas.

CENTRAL HEATING
Ducted Heatpumps are the holy grail of central heating and guess what? They can also cool and dehumidify your home. Ducted Heatpumps are often overlooked or priced out of reach by less experienced salesmen as its not just a point and shoot approach. We pride ourselves in our work with Ducted systems, we are able to provide quick and economic quotations and can provide expert advice on all the extra options on Ducted systems with zone control, fresh air integration, positive pressure solutions. We use the best materials when it comes to insulated ducting, mounting equipment, drainage materials. Every system we design is designed with the lowest possible decibel reading, least amount of static pressure and maximum effieciency with the help of the very latest software available.

VENTILATION
Home ventilation is a very important part of insuring you have a nice dry home to maximise the efficiency of your Heat pump. Whilst HRV systems are not designed to Heat your house they are designed to keep it dry, provide fresh filtered air to ensure your home healthy and easy to heat. We offer a number of solutions from integrated ducted heatpump systems to balanced heat recovery systems and positive air systems.

TESTIMONIALS
http://www.lotbazaro.co.nz/Browse/Listing.aspx?id=415728306

Target Market(s)

Home Owners

Industry/Entity Type

Air Conditioning

Colors
33a6d7
ffffff

Requirements
Must have
• Could possibly use the 'O' from Bramble Works logo throughout website - see business Card
Nice to have
• Bright & Crisp - White and Blue
• Would love to have our Logo used throughout the website.

```html
<!DOCTYPE html>
<html lang="en">
<head>
<meta charset="utf-8">
<title>Bramble Works – Heat Pumps, Air Conditioning &amp; Ventilation</title>
<link rel="stylesheet" href="https://fonts.googleapis.com/css2?family=Raleway:ital,wght@0,400;0,500;0,600;0,700;0,800;1,400&display=swap">
<style>
:root{
  --blue:#33a6d7;
  --blue-deep:#2a8cc0;
  --navy:#263a4c;
  --navy-deep:#1d2f3f;
  --ink:#222a30;
  --text:#555d63;
  --rule:#d9dde0;
  --light:#f4f5f6;
  --white:#ffffff;
}
*{box-sizing:border-box;margin:0;padding:0}
html,body{width:1200px;height:2922px;overflow:hidden}
body{font-family:"Raleway",Arial,sans-serif;color:var(--text);background:var(--white);position:relative}
a{color:inherit;text-decoration:none}

/* header */
.site-header{position:absolute;left:0;top:0;width:1200px;height:117px;background:var(--white)}
.brand{position:absolute;left:82px;top:30px;display:flex;align-items:center;gap:12px;color:var(--blue);font-weight:800;font-size:34px;letter-spacing:1px}
.brand-dot{width:26px;height:26px;border-radius:50%;background:var(--blue)}
.contact-strip{position:absolute;right:82px;top:16px;display:flex;gap:36px;font-size:17px;color:var(--ink)}
.contact-strip span{display:flex;align-items:center;gap:10px}
.icon-circle{width:34px;height:34px;border-radius:50%;background:var(--blue);display:flex;align-items:center;justify-content:center}
.header-rule{position:absolute;left:483px;right:80px;top:68px;height:1px;background:var(--rule)}
.main-nav{position:absolute;left:506px;top:82px;display:flex;gap:0;font-size:15px;font-weight:600;color:var(--ink)}
.main-nav a{display:block;padding:0 24px 10px}
.main-nav a.is-active{color:var(--blue);border-bottom:2px solid var(--blue)}

/* hero */
.hero{position:absolute;left:0;top:117px;width:1200px;height:526px;overflow:hidden}
.hero-photo{position:absolute;inset:0;background:linear-gradient(100deg,#8f9aa3 0%,#b4bdc4 30%,#9aa6ae 60%,#7d8a93 100%)}
.hero-title{position:absolute;left:460px;top:258px;width:580px;text-align:center;color:var(--white);font-size:31px;font-weight:700;line-height:42px;text-shadow:0 2px 6px rgba(0,0,0,.3)}
.hero-dots{position:absolute;left:722px;top:435px;display:flex;gap:6px}
.hero-dots i{width:14px;height:14px;border-radius:50%;background:var(--white);display:block}

/* shared heading */
.section-title{position:absolute;left:0;width:1200px;text-align:center;font-size:27px;font-weight:700;color:var(--ink);letter-spacing:.5px}
.section-title em,.col-title em{font-style:normal;color:var(--blue)}
.divider{position:absolute;left:343px;width:514px;height:20px}
.divider::before{content:"";position:absolute;left:0;right:0;top:9px;height:1px;background:var(--rule)}
.divider::after{content:"";position:absolute;left:246px;top:0;width:20px;height:20px;border-radius:50%;background:var(--white);border:2px solid #c9ced2}
.btn{display:inline-flex;align-items:center;justify-content:center;gap:6px;font-weight:600;font-size:14px}
.btn-blue{background:var(--blue);color:var(--white)}
.btn-white{background:var(--white);color:var(--blue)}

/* welcome */
.welcome-text{position:absolute;left:0;top:783px;width:1200px;text-align:center;font-size:14px;line-height:26px;color:var(--text)}
.welcome .btn{position:absolute;left:538px;top:918px;width:124px;height:39px}

/* services */
.services{position:absolute;left:0;top:1009px;width:1200px;height:413px;background:linear-gradient(90deg,#3aa6d9,#3d9fd0)}
.service{position:absolute;top:0;width:300px;height:413px;color:var(--white);text-align:center}
.service.is-blue{background:linear-gradient(180deg,#45acdd,#2f93c8)}
.service.is-dark{background:linear-gradient(180deg,#2f4354,#223446);clip-path:polygon(26px 0,274px 0,300px 26px,300px 387px,274px 413px,26px 413px,0 387px,0 26px)}
.service-badge{position:absolute;left:94px;top:42px;width:112px;height:112px;border-radius:50%;background:var(--white);display:flex;align-items:center;justify-content:center}
.service h3{position:absolute;left:0;top:187px;width:100%;font-size:20px;font-weight:700;letter-spacing:.5px}
.service p{position:absolute;left:30px;top:229px;width:240px;height:78px;overflow:hidden;font-size:13.5px;line-height:26px;font-weight:600}
.service .btn{position:absolute;left:91px;top:341px;width:118px;height:36px;font-size:13.5px}

/* gallery */
.gallery-row{position:absolute;left:80px;top:1574px;display:flex;gap:8px}
.gallery-item{width:254px;height:175px}

/* testimonials + why */
.trust{position:absolute;left:0;top:1808px;width:1200px;height:432px;background:var(--light)}
.col-title{position:absolute;top:46px;font-size:27px;font-weight:700;color:var(--ink)}
.col-rule{position:absolute;top:100px;height:1px;background:var(--rule)}
.col-split{position:absolute;left:598px;top:46px;width:0;height:340px;border-left:1px dashed #c5cacd}
.avatar{position:absolute;left:80px;top:131px;width:118px;height:118px;border-radius:50%;border:4px solid var(--white);box-shadow:0 0 0 2px var(--blue);background:linear-gradient(180deg,#c7d3dc,#7f97ab)}
.quote-mark{position:absolute;left:225px;top:100px;font-size:60px;color:#c3c8cc;font-family:Georgia,serif}
.quote{position:absolute;left:228px;top:116px;width:340px;font-style:italic;font-size:16px;line-height:26px;color:var(--ink)}
.client-name{position:absolute;left:228px;top:310px;font-size:19px;font-weight:600;color:var(--blue)}
.client-role{position:absolute;left:228px;top:340px;font-size:13px;color:var(--ink)}
.reasons-line{position:absolute;left:682px;top:158px;height:180px;border-left:2px dashed var(--blue)}
.reason{position:absolute;left:647px;width:474px}
.reason-icon{position:absolute;left:0;top:0;width:70px;height:70px;border-radius:50%;background:var(--blue);border:4px solid #cfe9f5;display:flex;align-items:center;justify-content:center}
.reason h4{position:absolute;left:97px;top:0;font-size:16px;font-weight:800;color:var(--ink)}
.reason p{position:absolute;left:97px;top:26px;width:360px;font-size:13.5px;line-height:24px;color:var(--text)}
.reason p b{color:var(--blue);font-weight:600}
.reason-rule{position:absolute;left:97px;top:78px;width:377px;height:1px;background:var(--rule)}

/* brands */
.brands-row{position:absolute;left:80px;top:2396px;display:flex;gap:27px}
.brand-box{width:150px;height:70px;border:1px solid var(--rule);background:var(--white);display:flex;align-items:center;justify-content:center;font-size:19px;font-weight:700;color:var(--ink)}
.arrow{position:absolute;top:2412px}

/* newsletter */
.newsletter{position:absolute;left:0;top:2513px;width:1200px;height:78px;background:var(--blue-deep)}
.newsletter-icon{position:absolute;left:114px;top:13px;width:52px;height:52px;border-radius:50%;border:2px solid var(--white);display:flex;align-items:center;justify-content:center}
.newsletter h2{position:absolute;left:193px;top:22px;font-size:26px;font-weight:600;color:var(--white)}
.newsletter-input{position:absolute;left:495px;top:19px;width:382px;height:40px;background:var(--white);font-size:13px;color:var(--ink);padding:11px 10px}
.newsletter-btn{position:absolute;left:892px;top:19px;width:193px;height:40px;background:var(--navy-deep);color:var(--white);font-size:17px;font-weight:700;letter-spacing:2px;display:flex;align-items:center;justify-content:center}

/* footer */
.site-footer{position:absolute;left:0;top:2591px;width:1200px;height:284px;background:linear-gradient(180deg,#2b4256,#223547);color:#d6dde3}
.foot-col{position:absolute;top:46px}
.foot-col h5{font-size:16px;font-weight:700;color:var(--white);letter-spacing:.5px;padding-bottom:12px;border-bottom:1px solid rgba(255,255,255,.2);margin-bottom:14px}
.foot-col h5 em{font-style:normal;color:var(--blue)}
.quick-links li{list-style:none;font-size:14px;line-height:31px}
.quick-links li::before{content:"›";color:var(--blue);margin-right:8px}
.quick-links li:first-child{color:var(--white);font-weight:700}
.contact-block{font-size:14px;line-height:30px}
.contact-block strong{color:var(--white);font-weight:700;display:block;line-height:22px}
.contact-line{display:flex;align-items:center;gap:12px}
.inquiry-field{width:224px;height:28px;background:var(--white);margin-bottom:8px;font-size:12px;color:#888;padding:6px 8px}
.inquiry-field.tall{height:28px}
.inquiry-btn{width:104px;height:29px;background:var(--blue);color:var(--white);font-size:15px;font-weight:700;display:flex;align-items:center;justify-content:center}
.social li{list-style:none;display:flex;align-items:center;gap:12px;font-size:12.5px;font-weight:700;color:var(--white);margin-bottom:20px}
.social i{width:32px;height:32px;border-radius:50%;background:var(--blue);display:block}
.copyright{position:absolute;left:0;top:2875px;width:1200px;height:47px;background:var(--blue);color:var(--white);font-size:13px;font-weight:600;text-align:center;line-height:47px}
</style>
</head>
<body>

<header class="site-header">
  <a class="brand" href="#"><span class="brand-dot"></span>BRAMBLE WORKS</a>
  <div class="contact-strip">
    <span><span class="icon-circle"><svg width="16" height="16" viewBox="0 0 24 24"><path fill="#fff" d="M6.6 10.8a15 15 0 0 0 6.6 6.6l2.2-2.2a1 1 0 0 1 1-.25 11.4 11.4 0 0 0 3.6.57 1 1 0 0 1 1 1V20a1 1 0 0 1-1 1A17 17 0 0 1 3 4a1 1 0 0 1 1-1h3.5a1 1 0 0 1 1 1c0 1.25.2 2.45.57 3.57a1 1 0 0 1-.25 1z"/></svg></span>022 418 6390</span>
    <span><span class="icon-circle"><svg width="16" height="16" viewBox="0 0 24 24"><path fill="#fff" d="M3 5h18v14H3z"/><path fill="none" stroke="#33a6d7" stroke-width="2" d="M3 6l9 7 9-7"/></svg></span>Marta.k@bramwks.co.nz</span>
  </div>
  <div class="header-rule"></div>
  <nav class="main-nav">
    <a class="is-active" href="#">HOME</a>
    <a href="#">ABOUT US</a>
    <a href="#">OUR SERVICES</a>
    <a href="#">PROJECT</a>
    <a href="#">CONTACT US</a>
  </nav>
</header>

<section class="hero">
  <div class="hero-photo" role="img" aria-label="Living room wall with a wall-mounted heat pump, two windows looking out to the sea and a potted tree"></div>
  <h1 class="hero-title">We Have Installed Thousands Of Heat Pumps And Also Specialise In Diagnostics And Repairs</h1>
  <div class="hero-dots"><i></i><i></i><i></i></div>
</section>

<section class="welcome">
  <h2 class="section-title" style="top:688px">WELCOME TO <em>BRAMBLE WORKS</em></h2>
  <div class="divider" style="top:736px"></div>
  <p class="welcome-text">Purchasing a Heatpump or Ventilation System can be a significant investment but it doesnt have to be a daunting one.<br>We have a team of nationally trained and qualified Refrigeration/HVAC and Electricians. We are factory trained and authorised to service and install all major<br>brands including Talvoro, Grenlo, Pelnor and Korrowane Electric, Veltrada and Osmelo units. We have installed thousands of heat pumps<br>and also specialise in diagnostics and repairs.</p>
  <a class="btn btn-blue" href="#">Read More <span>»</span></a>
</section>

<section class="services">
  <article class="service is-blue" style="left:0">
    <div class="service-badge"><svg width="52" height="30" viewBox="0 0 52 30"><rect x="2" y="2" width="48" height="16" rx="3" fill="none" stroke="#33a6d7" stroke-width="3"/><path d="M14 22v6M22 22v6M30 22v6M38 22v6" stroke="#33a6d7" stroke-width="2.5"/></svg></div>
    <h3>AIR CONDITIONING</h3>
    <p>Heat pumps are the most efficient way of using electricity to heat your home, but some are more efficient than others.</p>
    <a class="btn btn-white" href="#">Read More <span>»</span></a>
  </article>
  <article class="service is-dark" style="left:300px">
    <div class="service-badge"><svg width="36" height="40" viewBox="0 0 36 40"><rect x="4" y="2" width="28" height="36" fill="none" stroke="#263a4c" stroke-width="3"/><path d="M11 9h4M21 9h4M11 17h4M21 17h4M11 25h4M21 25h4M15 38v-7h6v7" stroke="#263a4c" stroke-width="2.5" fill="none"/></svg></div>
    <h3>COMMERCIAL</h3>
    <p>We have a growing Portfolio of clients that rely on us for their Commercial requirements. We have proven ourselves to be a force.</p>
    <a class="btn btn-white" href="#">Read More <span>»</span></a>
  </article>
  <article class="service is-blue" style="left:600px">
    <div class="service-badge"><svg width="44" height="38" viewBox="0 0 44 38"><path d="M6 6v26M14 6v26M22 6v26M30 6v26M38 6v26M2 10h40M2 28h40" stroke="#33a6d7" stroke-width="3" fill="none"/></svg></div>
    <h3>CENTRAL HEATING</h3>
    <p>Ducted Heatpumps are the holy grail of central heating and guess what? They can also cool and dehumidify your home.</p>
    <a class="btn btn-white" href="#">Read More <span>»</span></a>
  </article>
  <article class="service is-dark" style="left:900px">
    <div class="service-badge"><svg width="44" height="44" viewBox="0 0 44 44"><circle cx="22" cy="22" r="19" fill="none" stroke="#263a4c" stroke-width="3"/><circle cx="22" cy="22" r="3" fill="#263a4c"/><path d="M22 19c-2-6 0-11 4-11s3 6-4 11M25 22c6-2 11 0 11 4s-6 3-11-4M22 25c2 6 0 11-4 11s-3-6 4-11M19 22c-6 2-11 0-11-4s6-3 11 4" fill="#263a4c"/></svg></div>
    <h3>VENTILATION</h3>
    <p>Home ventilation is a very important part of insuring you have a nice dry home to maximise the efficiency of your Heat pump.</p>
    <a class="btn btn-white" href="#">Read More <span>»</span></a>
  </article>
</section>

<section class="gallery">
  <h2 class="section-title" style="top:1465px">PROJECT <em>GALLERY</em></h2>
  <div class="divider" style="top:1513px;left:443px;width:314px"></div>
  <div class="gallery-row">
    <div class="gallery-item" role="img" aria-label="Bright open-plan living room with staircase and timber floor" style="background:linear-gradient(135deg,#e9e4dc,#b9a48a)"></div>
    <div class="gallery-item" role="img" aria-label="Hand adjusting a thermostatic valve on a white radiator" style="background:linear-gradient(135deg,#d8dcdf,#f4f4f4 60%,#c9b6a6)"></div>
    <div class="gallery-item" role="img" aria-label="Modern bedroom with dark timber headboard and large window" style="background:linear-gradient(135deg,#4b3d33,#cfc6bb 60%,#f2efe9)"></div>
    <div class="gallery-item" role="img" aria-label="Ceiling cassette air conditioning unit with exposed ducting" style="background:linear-gradient(135deg,#f0f2f3,#c6ccd0)"></div>
  </div>
</section>

<section class="trust">
  <h2 class="col-title" style="left:82px">CLIENT <em>TESTIMONIALS</em></h2>
  <div class="col-rule" style="left:82px;width:490px"></div>
  <div class="avatar" role="img" aria-label="Portrait of a satisfied client"></div>
  <span class="quote-mark">“</span>
  <p class="quote">Lorem ipsum dolor sit amet, consectetuer adipiscing elit, sed diam nonummy nibh euismod tincidunt ut laoreet dolore magna aliquam erat volutpat. Ut wisi enim ad minim veniam, quis nostrud exerci tation ullamcorper suscipit lobortis nisl ut aliquip</p>
  <p class="client-name">Leena Harcourt</p>
  <p class="client-role">Marketing Manager</p>

  <div class="col-split"></div>

  <h2 class="col-title" style="left:648px">WHY CHOOSE <em>BRAMBLE WORKS</em></h2>
  <div class="col-rule" style="left:648px;width:472px"></div>
  <div class="reasons-line"></div>
  <div class="reason" style="top:123px">
    <div class="reason-icon"><svg width="28" height="28" viewBox="0 0 24 24"><path d="M4 12l5 5L20 6" fill="none" stroke="#fff" stroke-width="3"/></svg></div>
    <h4>EXPERIENCE COUNTS</h4>
    <p>We have a team of nationally trained and qualified Refrigeration/HVAC/Electrical Engineers and... <b>[+]</b></p>
    <div class="reason-rule"></div>
  </div>
  <div class="reason" style="top:211px">
    <div class="reason-icon"><svg width="28" height="28" viewBox="0 0 24 24"><path d="M12 2l3 6.5 7 .8-5.2 4.8 1.4 7L12 17.6 5.8 21l1.4-7L2 9.3l7-.8z" fill="#fff"/></svg></div>
    <h4>SATISFACTION GUARANTEE</h4>
    <p>We aim to please and I put my name behind our brand! We will take care of your project from... <b>[+]</b></p>
    <div class="reason-rule"></div>
  </div>
  <div class="reason" style="top:299px">
    <div class="reason-icon"><svg width="28" height="28" viewBox="0 0 24 24"><path d="M3 4h18v12H9l-5 4v-4H3z" fill="#fff"/></svg></div>
    <h4>LOW PRESSURE SALES</h4>
    <p>Nobody likes the vacuum salesmen's techniques and neither do we. We will come to your home... <b>[+]</b></p>
  </div>
</section>

<section class="brands">
  <h2 class="section-title" style="top:2286px">BRANDS WE <em>SERVE</em></h2>
  <div class="divider" style="top:2334px;left:463px;width:274px"></div>
  <svg class="arrow" style="left:38px" width="22" height="36" viewBox="0 0 22 36"><path d="M18 2L4 18l14 16" fill="none" stroke="#b9bfc3" stroke-width="3"/></svg>
  <div class="brands-row">
    <div class="brand-box">Norvane</div>
    <div class="brand-box">Korrowane</div>
    <div class="brand-box">Pelnor</div>
    <div class="brand-box">Veltrada</div>
    <div class="brand-box">Talvoro</div>
    <div class="brand-box">Osmelo</div>
  </div>
  <svg class="arrow" style="left:1142px" width="22" height="36" viewBox="0 0 22 36"><path d="M4 2l14 16L4 34" fill="none" stroke="#b9bfc3" stroke-width="3"/></svg>
</section>

<section class="newsletter">
  <div class="newsletter-icon"><svg width="26" height="20" viewBox="0 0 26 20"><rect x="1" y="1" width="24" height="18" fill="none" stroke="#fff" stroke-width="2"/><path d="M1 2l12 9 12-9" fill="none" stroke="#fff" stroke-width="2"/></svg></div>
  <h2>Sign Up For Newsletter</h2>
  <div class="newsletter-input">Enter your email here</div>
  <a class="newsletter-btn" href="#">SUBSCRIBE</a>
</section>

<footer class="site-footer">
  <div class="foot-col" style="left:82px;width:180px">
    <h5>QUICK <em>LINKS</em></h5>
    <ul class="quick-links"><li>Home</li><li>About Us</li><li>Services</li><li>Gallery</li><li>Contact Us</li></ul>
  </div>
  <div class="foot-col contact-block" style="left:321px;width:280px">
    <h5>CONTACT <em>DETAILS</em></h5>
    <strong>BRAMBLE WORKS</strong>
    <div>27 Harlow Crescent Petone, Wellington</div>
    <div class="contact-line"><svg width="14" height="14" viewBox="0 0 24 24"><path fill="#33a6d7" d="M6.6 10.8a15 15 0 0 0 6.6 6.6l2.2-2.2a1 1 0 0 1 1-.25 11.4 11.4 0 0 0 3.6.57 1 1 0 0 1 1 1V20a1 1 0 0 1-1 1A17 17 0 0 1 3 4a1 1 0 0 1 1-1h3.5a1 1 0 0 1 1 1c0 1.25.2 2.45.57 3.57a1 1 0 0 1-.25 1z"/></svg>022 418 6390</div>
    <div class="contact-line"><svg width="14" height="14" viewBox="0 0 24 24"><rect x="4" y="8" width="16" height="12" fill="#33a6d7"/><rect x="7" y="3" width="10" height="6" fill="none" stroke="#33a6d7" stroke-width="2"/></svg>022 418 6390</div>
    <div class="contact-line"><svg width="14" height="14" viewBox="0 0 24 24"><rect x="2" y="5" width="20" height="14" fill="#33a6d7"/></svg>Marta.k@bramwks.co.nz</div>
  </div>
  <div class="foot-col" style="left:668px;width:240px">
    <h5>QUICK <em>INQUIRY</em></h5>
    <div class="inquiry-field">Name</div>
    <div class="inquiry-field">Email</div>
    <div class="inquiry-field tall">Message</div>
    <a class="inquiry-btn" href="#">Submit</a>
  </div>
  <div class="foot-col" style="left:1003px;width:120px">
    <h5>FOLLOW <em>US</em></h5>
    <ul class="social"><li><i></i>FACELANE</li><li><i></i>CHIRPER</li><li><i></i>LINKROLL</li></ul>
  </div>
</footer>

<div class="copyright">Copyright © 2016 BRAMBLE WORKS. All Rights Reserved.</div>

</body>
</html>
```